Calendar Design Project: 2025 with Specific Edits

This is a straightforward project where your creativity can shine!
Simply take the existing 2024 calendar and adapt it for 2025 by incorporating the new photos I've attached.
Please keep the overall concept of the 2024 calendar intact—your focus will be on enhancing it with fresh visuals.

I can't wait to see your amazing designs!
I am looking for a talented graphic designer to create a new 2025 calendar with specific adjustments.
Pictures attached.
Requirements:
Calendar Size: 52cm x 34cm
March Folder:
Adjust the image named "attached - DJI-0025" to make the circular road darker to match the rest of the design.
May Folder:
Modify the circled area in the May image to ensure it looks consistent with the other road (reference file: "attached - After").
November Folder:
Clear out the circled area in the November image (reference file: "attached - After1").
Please let me know if you have any questions or need further clarification.
I added to my breif a design i made last year for same client.
2025, calendar should be vertical and not horizontal. and some of the photos attache are "Before" and "After" please include together inside each month of the calendar.
Thank you!
Feel free to adjust any details as necessary!

Hello talented designers!

I’m excited to share that this is my 14th project on the ArtHive platform, and I’ve been fortunate to have successful collaborations in the past. I'm looking forward to creating a new 2025 calendar with your help, and I believe that with your creativity and skills, we can make this project a success as well!

I hope to establish a long-term relationship with a talented team like yours. As an added incentive, I will be offering a bonus for the winner, and I may select more than one winner, so everyone has a chance to shine!

Let’s make something amazing together!

Best
Update:
cancel or before, only place the After picture

Requirements
Must have
• Project Overview Objective: Create a 2025 calendar using the provided images, maintaining the design concept from the 2024 calendar but enhancing it with new visuals. Format: Vertical layout (52cm x 34cm).

```html
<!DOCTYPE html>
<html lang="en">
<head>
<meta charset="utf-8">
<title>Tarsel Construction 2025 Calendar Cover</title>
<link rel="stylesheet" href="https://fonts.googleapis.com/css2?family=Bebas+Neue&family=Oswald:wght@400;500&display=swap">
<style>
  :root {
    --backdrop: #5cd59f;
    --ink: #1c1c1c;
    --ink-deep: #141414;
    --brand-green: #22b46a;
    --white: #ffffff;
    --paper: #f7f7f7;
    --muted: #d9d9d9;
    --photo-top: #c9ccc9;
    --photo-mid: #8f8d86;
    --photo-low: #9a7f5e;
  }
  * { margin: 0; padding: 0; box-sizing: border-box; }
  html, body {
    width: 1200px; height: 1164px; overflow: hidden;
    background: var(--backdrop);
  }
  .cover {
    position: absolute; left: 234px; top: 22px;
    width: 732px; height: 1120px;
    background: var(--ink);
    overflow: hidden;
    font-family: "Bebas Neue", "Oswald", sans-serif;
    color: var(--white);
  }
  .cover-photo {
    position: absolute; left: 0; top: 0; width: 100%; height: 760px;
    background: linear-gradient(180deg, var(--photo-top) 0%, var(--photo-mid) 55%, var(--photo-low) 100%);
  }
  .year-tab {
    position: absolute; left: 0; top: 0; width: 196px; height: 370px;
    background: var(--ink-deep);
    border-bottom-right-radius: 44px;
    text-align: center;
    padding-top: 20px;
  }
  .year-tab .year-top { font-size: 132px; line-height: 0.92; color: var(--white); display: block; }
  .year-tab .year-bottom { font-size: 132px; line-height: 0.92; color: var(--brand-green); display: block; }
  .year-tab .year-label { font-size: 40px; line-height: 1; letter-spacing: 1px; display: block; margin-top: 6px; }
  .brand-band { position: absolute; left: 0; top: 640px; width: 100%; height: 200px; }
  .brand-row {
    position: absolute; left: 62px; top: 752px;
    display: flex; align-items: center; gap: 14px;
    color: var(--ink);
  }
  .brand-mark { width: 30px; height: 30px; background: var(--brand-green); }
  .brand-name { font-size: 58px; line-height: 1; color: var(--ink); }
  .brand-divider { width: 3px; height: 58px; background: var(--brand-green); }
  .brand-legal { font-family: "Oswald", sans-serif; font-size: 20px; line-height: 1.2; color: var(--ink); }
  .headline {
    position: absolute; left: 62px; top: 866px;
    font-size: 60px; line-height: 1; letter-spacing: 0.5px;
  }
  .headline .reg { font-size: 26px; color: var(--brand-green); vertical-align: 28px; margin-left: 14px; }
  .address {
    position: absolute; left: 62px; top: 1004px;
    display: flex; align-items: center; gap: 10px;
    font-family: "Oswald", sans-serif; font-size: 15px; letter-spacing: 0.3px;
  }
  .contact-list {
    position: absolute; left: 62px; top: 1034px;
    list-style: none;
    font-family: "Oswald", sans-serif; font-size: 15px; letter-spacing: 0.3px;
  }
  .contact-list li { display: flex; align-items: center; gap: 10px; height: 22px; }
  .icon { width: 16px; height: 16px; flex: none; }
  .tagline {
    position: absolute; right: 40px; bottom: 26px;
    font-family: "Oswald", sans-serif; font-size: 11px; letter-spacing: 0.6px;
    color: var(--muted);
  }
  .tagline::before, .tagline::after { content: "•"; color: var(--brand-green); margin: 0 6px; }
</style>
</head>
<body>
  <main class="cover">
    <div class="cover-photo" role="img" aria-label="Photo of a concrete flyover under construction with red formwork gantry and excavators on site"></div>

    <div class="year-tab">
      <span class="year-top">20</span>
      <span class="year-bottom">25</span>
      <span class="year-label">CALENDER</span>
    </div>

    <svg class="brand-band" viewBox="0 0 732 200" preserveAspectRatio="none" aria-hidden="true">
      <path d="M0 110 C 180 40, 420 10, 732 0 L 732 176 L 0 176 Z" fill="#ffffff"/>
      <rect x="0" y="176" width="732" height="24" fill="#1c1c1c"/>
    </svg>

    <div class="brand-row">
      <span class="brand-mark"></span>
      <span class="brand-name">TARSEL</span>
      <span class="brand-divider"></span>
      <span class="brand-legal">TARSEL CONSTRUCTION<br>LIMITED</span>
    </div>

    <h1 class="headline">CIVIL ENGINEERING<br>&amp; CONSTRUCTION FIRM<span class="reg">RC - 4820193</span></h1>

    <p class="address">
      <svg class="icon" viewBox="0 0 16 16" aria-hidden="true"><path d="M8 1a5 5 0 0 0-5 5c0 4 5 9 5 9s5-5 5-9a5 5 0 0 0-5-5zm0 7a2 2 0 1 1 0-4 2 2 0 0 1 0 4z" fill="#22b46a"/></svg>
      42 HARLOW STREET, OFF MERIDIAN CRESCENT, EASTGATE, LAKEVIEW
    </p>

    <ul class="contact-list">
      <li>
        <svg class="icon" viewBox="0 0 16 16" aria-hidden="true"><path d="M3 1l3 3-1.5 2a9 9 0 0 0 5.5 5.5L12 10l3 3-2 2C7 15 1 9 1 3z" fill="#22b46a"/></svg>
        +1 555 010 4821
      </li>
      <li>
        <svg class="icon" viewBox="0 0 16 16" aria-hidden="true"><rect x="1" y="3" width="14" height="10" fill="#22b46a"/><path d="M1 3l7 6 7-6" stroke="#1c1c1c" stroke-width="1.4" fill="none"/></svg>
        INFO@TARSELBUILD.COM
      </li>
      <li>
        <svg class="icon" viewBox="0 0 16 16" aria-hidden="true"><circle cx="8" cy="8" r="6.5" fill="none" stroke="#22b46a" stroke-width="1.5"/><path d="M1.5 8h13M8 1.5c-3 3-3 10 0 13M8 1.5c3 3 3 10 0 13" fill="none" stroke="#22b46a" stroke-width="1.2"/></svg>
        WWW.TARSELBUILD.COM
      </li>
    </ul>

    <p class="tagline">Trusted Engineering, Lasting Results</p>
  </main>
</body>
</html>
```